I need a logo design for a new company based in Tucson called "Mindtrail Lee Corwin". I am a psychotherapist that specializes in clinical psychology with athletes and performers. The final design should incorporate the psychology symbol as a watermark. The logo should convey movement and fluidity. "Mindtrail" is a bit of a play on words combining psychology (head) with sports (coach). Other design interests include mid-century, Harold Ames Whitby. I will want to use the logo for business cards, letterhead and marketing brochures. I will put together a website at a later date. I am attaching a file with some pertinent information for the business card. Thank you.
Lee Corwin
mindtrailleecorwin@quillpost.net

Thank you all for the submissions so far.  I have submitted an additional file with a draft of a new design idea.  Since "mindtrail" is a bit of a play on words, I would like to see something with the two "H's" look something like quotation marks.  If the psychology logo is to be included at all, it needs to be less prominent.     Thank you all.  Lee                               

Target Market(s)

1) Adolescent and adult athletes and performers who are looking to increase their level of performance (Sport and Performance Psychology)
2) Adult psychotherapy patients (Clinical psychology)

Industry/Entity Type

Marketing

Colors

Designer to choose colors to be used in the design.

Requirements
Must have
• 1) Since "mindtrail" is a bit of a play on words, The "H's" need to be in a font that looks somewhat like quotation marks.

Nice to have
• Logo on one side. All other info on the backside?

```html
<!DOCTYPE html>
<html lang="en">
<head>
<meta charset="utf-8">
<title>Mindtrail Lee Corwin – Business Card</title>
<link rel="stylesheet" href="https://fonts.googleapis.com/css2?family=Cinzel:wght@500&family=Exo+2:wght@400;700&display=swap">
<style>
  :root {
    --backdrop: #e9e7e3;
    --card-white: #ffffff;
    --charcoal: #3f3f41;
    --charcoal-light: #5a5a5c;
    --gold: #d8a722;
    --gold-light: #e5bd4a;
    --ink: #2b2b2b;
    --text-light: #f6f6f6;
    --shadow: rgba(0,0,0,0.22);
  }
  * { box-sizing: border-box; margin: 0; padding: 0; }
  html, body { width: 1200px; height: 1018px; overflow: hidden; background: var(--backdrop); }
  .stage { position: relative; width: 1200px; height: 1018px; }

  .card {
    position: absolute; left: 250px; width: 700px; height: 400px;
    background: var(--card-white); overflow: hidden;
    box-shadow: 0 10px 28px var(--shadow);
  }
  .card--front { top: 84px; }
  .card--back  { top: 534px; }

  /* front */
  .brand { position: absolute; left: 44px; top: 110px; display: flex; align-items: center; gap: 22px; }
  .brand__dot { width: 96px; height: 96px; border-radius: 50%; background: var(--gold); flex: none; }
  .brand__name { font-family: "Cinzel", serif; font-weight: 500; font-size: 32px; color: var(--ink); letter-spacing: 1px; white-space: nowrap; }

  .contact-band {
    position: absolute; left: 0; top: 232px; width: 530px; height: 74px;
    background: linear-gradient(90deg, var(--charcoal) 0%, var(--charcoal-light) 60%, var(--charcoal) 100%);
    display: grid; grid-template-columns: 150px 1fr; grid-template-rows: 1fr 1fr;
    padding: 11px 0 11px 36px; align-items: center; column-gap: 16px;
  }
  .contact { display: flex; align-items: center; gap: 8px; font-family: "Exo 2", sans-serif; font-size: 14px; color: var(--text-light); letter-spacing: 0.4px; white-space: nowrap; }
  .contact svg { width: 14px; height: 14px; flex: none; }

  .gold-block {
    position: absolute; right: 0; top: 232px; width: 170px; height: 168px; background: var(--gold);
  }
  .person-band {
    position: absolute; left: 0; top: 306px; width: 700px; height: 94px;
    background: linear-gradient(90deg, var(--gold) 0%, var(--gold-light) 55%, var(--gold) 100%);
  }
  .person { position: absolute; left: 36px; top: 328px; color: var(--text-light); font-family: "Exo 2", sans-serif; }
  .person__name { font-weight: 700; font-size: 25px; letter-spacing: 1px; text-transform: uppercase; line-height: 1.05; }
  .person__role { font-size: 13px; letter-spacing: 2px; text-transform: uppercase; }
  .address { position: absolute; right: 22px; top: 246px; text-align: right; color: var(--text-light); font-family: "Exo 2", sans-serif; font-size: 15px; line-height: 1.5; letter-spacing: 0.4px; }

  .back-shapes { position: absolute; inset: 0; width: 100%; height: 100%; }
</style>
</head>
<body>
<main class="stage">
  <section class="card card--front" aria-label="Business card front">
    <div class="brand">
      <span class="brand__dot"></span>
      <span class="brand__name">Mindtrail Lee Corwin</span>
    </div>

    <div class="contact-band">
      <div class="contact">
        <svg viewBox="0 0 16 16" aria-hidden="true"><path fill="#f6f6f6" d="M3 1.5l2.6 0 1 3.3-1.6 1.2c.8 1.8 2.2 3.2 4 4l1.2-1.6 3.3 1v2.6c0 .6-.5 1-1 1C6.7 14 2 9.3 2 2.5c0-.5.4-1 1-1z"/></svg>
        <span>014 275 3860</span>
      </div>
      <div class="contact">
        <svg viewBox="0 0 16 16" aria-hidden="true"><rect x="1" y="3" width="14" height="10" fill="none" stroke="#f6f6f6" stroke-width="1.5"/><path d="M1 3l7 6 7-6" fill="none" stroke="#f6f6f6" stroke-width="1.5"/></svg>
        <span>hello@mindtrail.net</span>
      </div>
      <div class="contact">
        <svg viewBox="0 0 16 16" aria-hidden="true"><rect x="4" y="1" width="8" height="14" rx="1.5" fill="none" stroke="#f6f6f6" stroke-width="1.5"/><circle cx="8" cy="12.5" r="0.9" fill="#f6f6f6"/></svg>
        <span>014 275 3860</span>
      </div>
      <div class="contact">
        <svg viewBox="0 0 16 16" aria-hidden="true"><circle cx="8" cy="8" r="6.5" fill="none" stroke="#f6f6f6" stroke-width="1.3"/><ellipse cx="8" cy="8" rx="2.8" ry="6.5" fill="none" stroke="#f6f6f6" stroke-width="1.1"/><path d="M1.5 8h13" stroke="#f6f6f6" stroke-width="1.1"/></svg>
        <span>www.mindtrailcoach.net</span>
      </div>
    </div>

    <div class="person-band"></div>
    <div class="gold-block"></div>
    <div class="person">
      <div class="person__name">Nora Pell</div>
      <div class="person__role">General Manager</div>
    </div>
    <div class="address">42 Saguaro Vale Road,<br>2nd floor Suite B.</div>
  </section>

  <section class="card card--back" aria-label="Business card back">
    <svg class="back-shapes" viewBox="0 0 700 400" preserveAspectRatio="none" aria-hidden="true">
      <polygon points="0,0 150,0 0,130" fill="#d8a722"/>
      <polygon points="330,0 470,0 250,400 110,400" fill="#d8a722"/>
      <polygon points="700,250 700,400 560,400" fill="#d8a722"/>
    </svg>
  </section>
</main>
</body>
</html>
```